Risk Management Company in need of Business Card Design

We sell risk management insurance to Lenders (Banks, Credit Unions, Real Estate Trust).

We need a very clean, professional card that will leave a great impression.

We are looking to use a blue color for our logo on the card (Preferably close to royal blue but are open to looking at navy blue or any darker blues as well).

Please see the logo attached to get an idea. We are open to writing Harbor Ledger Under the logo or next to the logo. Really whatever looks best.

Target Market(s)

Banks, Credit Unions, Real Estate Trusts

Industry/Entity Type

Insurance

Contact Information for Business Card

Name: Tom Brandish
Title: Regional Sales Director
Email: tbrandish@harborledger-example.net
C:410-555-0137
D:410-555-0182
888-555-0149 Ext.318
F:443-555-0164 (We would like to see some cards without the fax number as well to compare)

Company Name: Harbor Ledger
Website: www.harborledger-example.net

Address: 718 E. Marlow St. Suite 340, Larkfield, MD 21287 (Preferably written on the bottom of the card in small print.)

Colors
0355a3
0455a3

Requirements
Nice to have
• We would like to see a couple of where the back has the logo in reverse colors (Logo White, Background Blue)

```html
<!DOCTYPE html>
<html lang="en">
<head>
<meta charset="utf-8">
<title>Harbor Ledger – Business Cards</title>
<link rel="stylesheet" href="https://fonts.googleapis.com/css2?family=Source+Sans+3:wght@400;600;700&display=swap">
<style>
  :root {
    --royal: #0455a3;
    --slate: #34505a;
    --ink: #333333;
    --icon: #555555;
    --rule: #c9c9c9;
    --grey: #8c8c8c;
    --black: #141414;
    --paper: #ffffff;
    --backdrop: #e8e8e6;
  }
  * { box-sizing: border-box; margin: 0; padding: 0; }
  html, body {
    width: 1200px; height: 786px; overflow: hidden;
    background: var(--backdrop);
    font-family: "Source Sans 3", "Myriad Pro", Arial, sans-serif;
    color: var(--ink);
  }
  .sheet {
    position: relative; width: 1200px; height: 786px;
    display: grid;
    grid-template-columns: 540px 540px;
    grid-template-rows: 300px 300px;
    gap: 40px;
    padding: 73px 40px;
  }
  .card {
    position: relative; overflow: hidden;
    background: var(--paper);
    box-shadow: 0 2px 10px rgba(0,0,0,.18);
  }

  /* wordmark */
  .wordmark {
    display: flex; align-items: center; justify-content: center; gap: 12px;
    font-weight: 600; text-transform: uppercase; letter-spacing: .08em;
    white-space: nowrap;
  }
  .wordmark-square { display: block; flex: none; }
  .card-front .wordmark {
    position: absolute; top: 62px; left: 0; right: 0;
    font-size: 26px;
  }
  .card-front .wordmark-square { width: 22px; height: 22px; }

  .theme-slate .wordmark { color: var(--slate); }
  .theme-slate .wordmark-square { background: var(--slate); }
  .theme-royal .wordmark { color: var(--royal); }
  .theme-royal .wordmark-square { background: var(--royal); }

  /* person block */
  .person {
    position: absolute; left: 0; width: 268px; top: 146px;
    text-align: right;
  }
  .person-name { font-size: 18px; font-weight: 600; line-height: 22px; }
  .theme-slate .person-name { color: var(--ink); }
  .theme-royal .person-name { color: var(--royal); }
  .person-title { font-size: 16px; line-height: 21px; }
  .address { margin-top: 18px; font-size: 14px; line-height: 18px; }

  .divider {
    position: absolute; left: 282px; top: 140px; width: 1px; height: 118px;
    background: var(--rule);
  }

  /* contact list */
  .contacts {
    position: absolute; left: 294px; top: 138px;
    list-style: none; font-size: 13px; line-height: 21px; white-space: nowrap;
  }
  .contacts li { display: flex; align-items: center; gap: 4px; }
  .contacts svg { width: 10px; height: 10px; fill: var(--icon); flex: none; }
  .contacts .ext { font-size: 9px; position: relative; top: -4px; margin-left: 2px; }
  .contacts .spacer { width: 6px; }

  .edge-bands {
    position: absolute; left: 0; bottom: 0; width: 540px; height: 40px;
  }
  .band-blue { fill: var(--royal); }
  .band-grey { fill: var(--grey); }
  .band-black { fill: var(--black); }

  /* backs */
  .card-back-blue { background: var(--royal); color: var(--paper); }
  .card-back-blue .wordmark {
    position: absolute; left: 0; right: 0; top: 100px;
    font-size: 46px; color: var(--paper);
  }
  .card-back-blue .wordmark-square { width: 34px; height: 34px; background: var(--paper); }
  .website {
    position: absolute; left: 0; right: 0; text-align: center;
    font-size: 17px; font-weight: 600; letter-spacing: .14em;
  }
  .card-back-blue .website { top: 170px; color: var(--paper); }

  .card-back-white .wordmark {
    position: absolute; left: 0; right: 0; top: 110px;
    font-size: 42px;
  }
  .card-back-white .wordmark-square { width: 32px; height: 32px; }
  .card-back-white .website { top: 178px; color: var(--ink); font-weight: 400; }
</style>
</head>
<body>
<main class="sheet">

  <!-- front, slate variant -->
  <article class="card card-front theme-slate">
    <div class="wordmark"><span class="wordmark-square"></span>Harbor Ledger</div>
    <div class="person">
      <p class="person-name">Tom Brandish</p>
      <p class="person-title">Regional Sales Director</p>
      <p class="address">718 E. Marlow St.<br>Suite 340, Larkfield<br>MD 21287</p>
    </div>
    <div class="divider"></div>
    <ul class="contacts">
      <li><svg viewBox="0 0 10 10"><rect x="2.5" y="0" width="5" height="10" rx="1"/></svg>410-555-0137</li>
      <li><svg viewBox="0 0 10 10"><circle cx="5" cy="5" r="5"/></svg>888-555-0149<span class="ext">Ext.318</span></li>
      <li><svg viewBox="0 0 10 10"><rect x="0" y="3" width="10" height="7"/><rect x="2" y="0" width="6" height="3"/></svg>443-555-0164<span class="spacer"></span><svg viewBox="0 0 10 10"><circle cx="5" cy="5" r="5"/></svg>410-555-0182</li>
      <li><svg viewBox="0 0 10 10"><path d="M0 2h10v8H0z"/></svg>tbrandish@harborledger-example.net</li>
      <li><svg viewBox="0 0 10 10"><circle cx="5" cy="5" r="5"/></svg>www.harborledger-example.net</li>
    </ul>
    <svg class="edge-bands" viewBox="0 0 540 40" aria-hidden="true">
      <polygon class="band-grey" points="0,28 262,28 254,40 0,40"/>
      <polygon class="band-blue" points="280,24 540,4 540,18 262,40 254,40"/>
    </svg>
  </article>

  <!-- front, royal variant -->
  <article class="card card-front theme-royal">
    <div class="wordmark"><span class="wordmark-square"></span>Harbor Ledger</div>
    <div class="person">
      <p class="person-name">Tom Brandish</p>
      <p class="person-title">Regional Sales Director</p>
      <p class="address">718 E. Marlow St.<br>Suite 340, Larkfield<br>MD 21287</p>
    </div>
    <div class="divider"></div>
    <ul class="contacts">
      <li><svg viewBox="0 0 10 10"><rect x="2.5" y="0" width="5" height="10" rx="1"/></svg>410-555-0137</li>
      <li><svg viewBox="0 0 10 10"><circle cx="5" cy="5" r="5"/></svg>888-555-0149<span class="ext">Ext.318</span></li>
      <li><svg viewBox="0 0 10 10"><rect x="0" y="3" width="10" height="7"/><rect x="2" y="0" width="6" height="3"/></svg>443-555-0164<span class="spacer"></span><svg viewBox="0 0 10 10"><circle cx="5" cy="5" r="5"/></svg>410-555-0182</li>
      <li><svg viewBox="0 0 10 10"><path d="M0 2h10v8H0z"/></svg>tbrandish@harborledger-example.net</li>
      <li><svg viewBox="0 0 10 10"><circle cx="5" cy="5" r="5"/></svg>www.harborledger-example.net</li>
    </ul>
    <svg class="edge-bands" viewBox="0 0 540 40" aria-hidden="true">
      <polygon class="band-black" points="0,26 248,26 236,40 0,40"/>
      <polygon class="band-blue" points="266,24 540,4 540,18 252,40 240,40"/>
    </svg>
  </article>

  <!-- back, reversed -->
  <article class="card card-back-blue">
    <div class="wordmark"><span class="wordmark-square"></span>Harbor Ledger</div>
    <p class="website">www.harborledger-example.net</p>
  </article>

  <!-- back, white -->
  <article class="card card-back-white theme-royal">
    <div class="wordmark"><span class="wordmark-square"></span>Harbor Ledger</div>
    <p class="website">www.harborledger-example.net</p>
  </article>

</main>
</body>
</html>
```